Business Intelligence Application - Reporting Menu and Report Criteria Design

Looking for a fresh, effective and user friendly view for the menu structure and reporting criteria screen format for a business reporting application. Initial format completed, content structure is in place, but we need the 'wow' design.. as its a serious professional report/BI tool it has to fall within certain guidelines for clarity and graphics..but we want it to be slick, friendly, great user experience. There is a large amount of complex content to fit into a small space and we need it to be very inviting, modern and intuitive.. If interested, please review the attachment. We have live screens in operation, but feel these could be improved and looking forward to seeing what great creative suggestions could be made. Please review work done to date in the attached.. We are not looking for a total re-design of everything, all the basic business content/structure is there.. but tell us what we could do to improve this in terms of graphic design... particularly the criteria screens.. thanks!
Updates

Reason: Need a few more days to review designs - thanks for all submissions so far, we will make a selection shortly.

Target Market(s)

Business analysts, hotel operations teams, finance analysts hospitality industry

Industry/Entity Type

Hospitality

Coding

Coded - Design and coding required

Number of Pages Required

4 page

Font styles to use
Sans Serif
Other font styles liked:
• Candara, please see example in deck

Colors
3276b5
3176b5
0255a3
85acd3
33a6d7
cee9f5
85cae6

Requirements
Must have
• sharp clear, logical menu structure, (currently it has 'clicks to sub-menus, we need hover over, slide to sub-menus..) colour, styling.. and most focus on revision of criteria.. right now is somewhat heavy, cumbersome.. keep colour and friendly intuitive process steps.. its heavy analytical stuff.. best of luck!
Should not have
• No grey fonts on white or grey screens! many business apps are not readable or sharp.. or fonts are too small.. colourless, so please avoid that.. see our deck - sharp dark (navy) or black fonts on white, or light shading..

```html
<!DOCTYPE html>
<html lang="en">
<head>
<meta charset="utf-8">
<title>Yield Insight – Property Search</title>
<link rel="stylesheet" href="https://fonts.googleapis.com/css2?family=Lato:ital,wght@0,400;0,700;0,900;1,400&display=swap">
<style>
  :root {
    --navy-deep: #04193a;
    --nav-blue: #0255a3;
    --nav-active: #0a4a8c;
    --nav-line: #3176b5;
    --accent: #33a6d7;
    --accent-soft: #85acd3;
    --cyan-brand: #33d2f0;
    --ink: #2b2b2b;
    --ink-soft: #4a4a4a;
    --line: #cfcfcf;
    --tab-bg: #e6e6e6;
    --panel-bg: #f2f2f2;
    --page-bg: #ededed;
    --white: #ffffff;
  }
  * { box-sizing: border-box; margin: 0; padding: 0; }
  html, body { width: 1200px; height: 736px; overflow: hidden; }
  body {
    position: relative;
    font-family: "Lato", sans-serif;
    color: var(--ink);
    background: var(--page-bg);
  }
  .sidebar {
    position: absolute; left: 0; top: 0; width: 252px; height: 736px;
    background: var(--nav-blue);
  }
  .brand {
    height: 82px; background: var(--navy-deep);
    display: flex; align-items: center; padding-left: 46px; gap: 12px;
  }
  .brand-mark { width: 22px; height: 22px; border-radius: 50%; background: var(--accent-soft); }
  .brand-name { color: var(--cyan-brand); font-size: 21px; font-weight: 700; }
  .menu { list-style: none; margin-top: 17px; }
  .menu-item {
    height: 71px; display: flex; align-items: center; padding-left: 33px; gap: 20px;
    color: var(--white); font-weight: 700; font-size: 15.5px; letter-spacing: .2px;
    border-bottom: 1px solid var(--nav-line);
  }
  .menu-item:nth-child(2), .menu-item:nth-child(3) { border-bottom: none; }
  .menu-item.is-active { background: var(--nav-active); height: 63px; margin-bottom: 8px; }
  .menu-item.last { border-bottom: none; }
  .menu-icon { width: 24px; height: 22px; fill: var(--white); flex: none; }

  .topbar {
    position: absolute; left: 252px; top: 0; width: 948px; height: 82px;
    background: var(--white); box-shadow: 0 1px 3px rgba(0,0,0,.12);
  }
  .avatar {
    position: absolute; left: 534px; top: 15px; width: 54px; height: 54px; border-radius: 50%;
    background: #8eb3dc; border: 3px solid #e9eef3; overflow: hidden;
  }
  .welcome { position: absolute; left: 604px; top: 20px; font-size: 15.5px; font-weight: 700; color: var(--ink); }
  .date { position: absolute; left: 604px; top: 47px; font-size: 12px; font-style: italic; color: var(--ink-soft); display: flex; gap: 6px; align-items: center; }
  .round-btn {
    position: absolute; top: 21px; width: 40px; height: 40px; border-radius: 50%;
    border: 1px solid #9a9a9a; display: flex; align-items: center; justify-content: center;
  }
  .round-btn svg { width: 15px; height: 15px; fill: var(--accent); }

  .view-bar {
    position: absolute; left: 292px; top: 114px; width: 856px; height: 47px;
    background: var(--white); border: 1px solid #bdbdbd;
    font-size: 14px; color: var(--ink-soft); padding: 16px 19px;
  }
  .view-badge {
    position: absolute; right: 0; top: 0; width: 58px; height: 45px; border-left: 1px solid #bdbdbd;
    display: flex; align-items: center; justify-content: center;
  }
  .view-badge span { width: 34px; height: 34px; border-radius: 50%; background: #c9955a; }

  .tabs { position: absolute; left: 292px; top: 199px; width: 856px; display: flex; gap: 10.4px; }
  .tab {
    flex: 1; height: 50px; background: var(--tab-bg); border: 1px solid #c4c4c4;
    display: flex; align-items: center; justify-content: center; text-align: center;
    font-size: 15px; font-weight: 700; line-height: 1.2; color: var(--ink);
  }
  .tab.is-active { background: var(--accent); border-color: var(--accent); color: var(--white); }

  .suggest { position: absolute; left: 292px; top: 249px; width: 191px; background: var(--white); border: 1px solid #9a9a9a; z-index: 2; }
  .suggest-query { height: 34px; padding: 9px 0 0 45px; font-size: 11.5px; border-bottom: 1px solid #9a9a9a; }
  .suggest-hit { height: 34px; padding: 8px 0 0 45px; font-size: 14.5px; }

  .property-card {
    position: absolute; left: 291px; top: 308px; width: 467px; height: 309px;
    background: var(--white); border-top: 3px solid var(--accent);
    box-shadow: 0 1px 3px rgba(0,0,0,.18);
  }
  .card-title { height: 48px; background: var(--panel-bg); padding: 15px 27px 0; font-size: 21.5px; font-weight: 900; color: var(--ink); }
  .property-list { list-style: none; margin: 18px 0 0 25px; width: 392px; }
  .property-row {
    display: flex; justify-content: space-between; padding: 0 36px 0 2px;
    height: 43px; align-items: center; border-bottom: 1px solid var(--line);
    font-size: 14px; color: var(--ink-soft);
  }
  .property-row:first-child { height: 40px; align-items: flex-start; padding-top: 4px; }
  .scroll-track { position: absolute; right: 0; top: 51px; width: 20px; height: 255px; border-left: 1px solid #dedede; }
  .scroll-track::before, .scroll-track::after { content: ""; position: absolute; left: 6px; border: 4px solid transparent; }
  .scroll-track::before { top: 6px; border-bottom-color: #aaa; }
  .scroll-track::after { bottom: 6px; border-top-color: #aaa; }

  .footer-rule { position: absolute; left: 292px; top: 655px; width: 809px; border-top: 1px solid #9a9a9a; }
  .copyright { position: absolute; left: 292px; top: 688px; width: 809px; text-align: center; font-size: 12px; color: var(--ink-soft); }
</style>
</head>
<body>
  <aside class="sidebar">
    <div class="brand"><span class="brand-mark"></span><span class="brand-name">Yield Insight</span></div>
    <ul class="menu">
      <li class="menu-item">
        <svg class="menu-icon" viewBox="0 0 24 22"><circle cx="12" cy="6" r="5"/><path d="M3 21c0-6 4-8 9-8s9 2 9 8z"/></svg>ADMIN
      </li>
      <li class="menu-item">
        <svg class="menu-icon" viewBox="0 0 24 22"><circle cx="12" cy="5" r="4"/><circle cx="4.5" cy="8" r="3"/><circle cx="19.5" cy="8" r="3"/><path d="M5 21c0-5 3-7 7-7s7 2 7 7z"/><path d="M0 19c0-4 2-6 5-6l1 1c-1 1-2 3-2 5z"/><path d="M24 19c0-4-2-6-5-6l-1 1c1 1 2 3 2 5z"/></svg>MANAGEMENT
      </li>
      <li class="menu-item is-active">
        <svg class="menu-icon" viewBox="0 0 24 22"><circle cx="10" cy="9" r="6.5" fill="none" stroke="#fff" stroke-width="3"/><path d="M14.5 13.5l6 6" stroke="#fff" stroke-width="4" stroke-linecap="round"/></svg>PROPERTY SEARCH
      </li>
      <li class="menu-item">
        <svg class="menu-icon" viewBox="0 0 24 22"><circle cx="9" cy="11" r="5.5" fill="none" stroke="#fff" stroke-width="3.5" stroke-dasharray="2.5 1.8"/><circle cx="19" cy="6" r="3" fill="none" stroke="#fff" stroke-width="2.5" stroke-dasharray="1.6 1.2"/><circle cx="19" cy="17" r="3" fill="none" stroke="#fff" stroke-width="2.5" stroke-dasharray="1.6 1.2"/></svg>INTEL
      </li>
      <li class="menu-item last">
        <svg class="menu-icon" viewBox="0 0 24 22"><path d="M12 1a6 6 0 0 0-4 10.5V15h8v-3.5A6 6 0 0 0 12 1z" fill="none" stroke="#fff" stroke-width="2"/><rect x="9" y="16.5" width="6" height="2"/><rect x="10" y="19.5" width="4" height="2"/></svg>PLANNING
      </li>
    </ul>
  </aside>

  <header class="topbar">
    <div class="avatar" role="img" aria-label="User profile picture placeholder"></div>
    <p class="welcome">Welcome Admin</p>
    <p class="date">
      <svg width="11" height="11" viewBox="0 0 11 11"><rect x=".5" y="1.5" width="10" height="9" fill="none" stroke="#888"/><rect x=".5" y="1.5" width="10" height="2.5" fill="#888"/></svg>
      Tuesday October 03, 2017
    </p>
    <div class="round-btn" style="left:800px">
      <svg viewBox="0 0 16 16"><path d="M8 1a4.5 4.5 0 0 0-4.5 4.5V10L2 12h12l-1.5-2V5.5A4.5 4.5 0 0 0 8 1z"/><circle cx="8" cy="14" r="1.8"/></svg>
    </div>
    <div class="round-btn" style="left:858px">
      <svg viewBox="0 0 16 16"><path d="M1 3h6v2H3v6h4v2H1z"/><path d="M8 5h3V2l5 6-5 6v-3H8z"/></svg>
    </div>
  </header>

  <div class="view-bar">My View
    <div class="view-badge"><span role="img" aria-label="Integration app badge"></span></div>
  </div>

  <nav class="tabs">
    <div class="tab is-active">SEARCH<br>NAME</div>
    <div class="tab">SEARCH ID</div>
    <div class="tab">SEARCH<br>PRODUCT</div>
    <div class="tab">DIVISIONS</div>
    <div class="tab">REGIONS</div>
    <div class="tab">AREAS</div>
  </nav>

  <div class="suggest">
    <div class="suggest-query">Royal...</div>
    <div class="suggest-hit">Royal Beach Hotel</div>
  </div>

  <section class="property-card">
    <h2 class="card-title">SELECT PROPERTY</h2>
    <ul class="property-list">
      <li class="property-row"><span>Grand Central Hotel &amp; Towers</span><span>RHDOH</span></li>
      <li class="property-row"><span>Sandy Beach Hotel</span><span>123</span></li>
      <li class="property-row"><span>Grand Central Hotel &amp; Towers</span><span>RHDOH</span></li>
      <li class="property-row"><span>Sandy Beach Hotel</span><span>123</span></li>
    </ul>
    <div class="scroll-track"></div>
  </section>

  <div class="footer-rule"></div>
  <p class="copyright">Copyright © 2017, Yield Insight. All rights reserved.</p>
</body>
</html>
```